Vibrant, yet professional, stationery set and other designs required.

I need to source a fantastic designer for a new project as part of my company using a new logo designed via sketch harbor.

**UPDATE** I am not looking for just 'fine' design that will suffice. I am looking for something great.

We are a life assurance brokerage based in Dublin, Ireland and BrightRoost.ie is our new website aimed at providing services for young families in Ireland. We are hoping to be the 'Velro' level of service providers in this area and I am looking for the quality of design to reflect this :-) Hopefully that makes sense!

I have a preference for straight lines over curves and waves.

I need...

1. Business card
2. Letterhead
3. Banner (for printing - 76cm X 305cm)
4. Car branding for KORVA 9 (2014 sport model) I believe the templates are freely available online.

Target Market(s)

Parents in Ireland - Aged 27 to 50.

Industry/Entity Type

Financial Planning

Colors

Designer to choose colors to be used in the design.

Requirements
Must have
• All of the items listed in the description above. I like clean, bright, legible, vibrant and professional design.
Should not have
• No silly or 'cheap' looking designs. This is a professional company looking to provide a professional service.

```html
<!DOCTYPE html>
<html lang="en">
<head>
<meta charset="utf-8">
<title>BrightRoost.ie business card</title>
<link rel="stylesheet" href="https://fonts.googleapis.com/css2?family=Jost:wght@400;500;600&display=swap">
<style>
  :root {
    --backdrop: #c9c9c9;
    --orange: #f0821a;
    --card-white: #f7f7f6;
    --slate: #8a9396;
    --ink: #4a4a4a;
    --white: #ffffff;
  }
  * { margin: 0; padding: 0; box-sizing: border-box; }
  html, body { width: 1200px; height: 960px; overflow: hidden; }
  body {
    background: var(--backdrop);
    font-family: "Jost", sans-serif;
    position: relative;
  }
  .card {
    position: absolute;
    left: 320px;
    width: 600px;
    height: 342px;
    box-shadow: 0 3px 8px rgba(0,0,0,0.25);
  }
  .card-front {
    top: 100px;
    background: var(--orange);
    color: var(--white);
  }
  .front-brand {
    position: absolute;
    top: 218px;
    left: 0; right: 0;
    text-align: center;
    font-size: 62px;
    font-weight: 500;
    letter-spacing: -0.5px;
    line-height: 1;
  }
  .front-web {
    position: absolute;
    top: 294px;
    left: 0; right: 0;
    text-align: center;
    font-size: 14px;
    letter-spacing: 6px;
  }
  .card-back {
    top: 493px;
    background: var(--card-white);
  }
  .accent-bar {
    position: absolute;
    left: 0; top: 28px;
    width: 7px; height: 40px;
    background: var(--orange);
  }
  .person-name {
    position: absolute;
    left: 27px; top: 26px;
    font-size: 20px;
    font-weight: 600;
    color: var(--orange);
    letter-spacing: 0.3px;
  }
  .person-role {
    position: absolute;
    left: 27px; top: 52px;
    font-size: 15px;
    font-weight: 600;
    color: var(--slate);
    letter-spacing: 0.5px;
  }
  .address {
    position: absolute;
    left: 27px; top: 174px;
    font-size: 14px;
    color: var(--ink);
    line-height: 18px;
    font-style: normal;
  }
  .contact-list {
    position: absolute;
    left: 27px; top: 219px;
    list-style: none;
    font-size: 14px;
    color: var(--ink);
  }
  .contact-list li {
    display: flex;
    align-items: center;
    height: 19.3px;
  }
  .contact-list svg {
    width: 14px; height: 14px;
    margin-right: 9px;
    fill: var(--orange);
  }
  .back-brand {
    position: absolute;
    right: 26px; top: 236px;
    font-size: 42px;
    font-weight: 500;
    color: var(--slate);
    line-height: 1;
    letter-spacing: -0.5px;
  }
</style>
</head>
<body>
  <section class="card card-front">
    <div class="front-brand">BrightRoost.ie</div>
    <div class="front-web">www.brightroost.ie</div>
  </section>

  <section class="card card-back">
    <div class="accent-bar"></div>
    <h1 class="person-name">OWEN TIERNEY</h1>
    <h2 class="person-role">CEO/FOUNDER</h2>
    <address class="address">42 Larchfield Row<br>Ranelagh, Dublin D06 K2P8</address>
    <ul class="contact-list">
      <li><svg viewBox="0 0 16 16"><path d="M3.5 1l2.5 3-1.5 2c1 2 3 4 5 5l2-1.5 3 2.5-1.5 2.5C7 15 1 9 1 2.5z"/></svg>015 230 4471</li>
      <li><svg viewBox="0 0 16 16"><path d="M4 0h8a1 1 0 0 1 1 1v14a1 1 0 0 1-1 1H4a1 1 0 0 1-1-1V1a1 1 0 0 1 1-1zm1 2v10h6V2zm3 11a1 1 0 1 0 0 2 1 1 0 0 0 0-2z"/></svg>087 612 3390</li>
      <li><svg viewBox="0 0 16 16"><path d="M4 1h8v4H4zM1 6h14v6h-3v3H4v-3H1zm4 4v4h6v-4z"/></svg>015 230 4472</li>
      <li><svg viewBox="0 0 16 16"><path d="M1 3h14v1L8 9 1 4zm0 3l7 5 7-5v7H1z"/></svg>owen@brightroost.ie</li>
      <li><svg viewBox="0 0 16 16"><path d="M8 1a7 7 0 1 0 0 14A7 7 0 0 0 8 1zm-1 2.5c1 .5 1 2 0 2.5-1 .8-3 .5-3 2s2 1 2 2.5-.5 2.5 0 3A5.5 5.5 0 0 1 7 3.5zm3 .5c1.5.5 3 2 3 4-1 0-2-1-2.5-.5S11 9 10 10s-1-1.5-2-2 1-3 2-4z"/></svg>www.brightroost.ie</li>
    </ul>
    <div class="back-brand">BrightRoost.ie</div>
  </section>
</body>
</html>
```